interior designer/stylist looking for a letter press business card to reflect the stylish work

Hello Designers,
I need a business card design for an company called Mosaic Interior Design. I'm aiming at the high end residential and private client market in London providing sleek simple interiors. I'd like my business card to be pinterest worthy and expensive looking, i want people to pin it and for it to have a sought after look, and want prospective customers to hire me as their interior designer as my card is so beautiful.
I love letter press design. I also like the use of colour/foil on the edge.
Colour combos & general things I like -
Black and White
Navy Blue and Gold
Neutral colours (muted palette of greys whites navys beiges)
White Marble & brass
Vorelle (fashion designer)
....also open to other suggestions....
Please dont take the pink in the attached photos too literally. i'd like the card to look more masculine than feminine.
I'd like Mosaic on one side in one font, with interior design underneath so one word will make the statement....... unless anyone has any other ideas, open to suggestions.
I'd like a really simple font and for the whole card to look very graphic.
my details -
Petra Wendlecombe
Interior Designer & Stylist
email petra@mosaicinteriordesign.co.uk
phone +447311584209
website wwww.mosaicinteriordesign.co.uk
GO GO GO!! EXCITED TO SEE THE OUTCOME!!
x P
Target Market(s)
High End Residential and private clients
Industry/Entity Type
Business
Contact Information for Business Card
Mosaic Interior Design & Styling
Petra Wendlecombe
phone +447311584209

```html
<!DOCTYPE html>
<html lang="en">
<head>
<meta charset="utf-8">
<title>Mosaic Interior Design – Business Card</title>
<link rel="stylesheet" href="https://fonts.googleapis.com/css2?family=Open+Sans:wght@400;600&display=swap">
<style>
  :root {
    --backdrop: #3a322e;
    --card: #141414;
    --card-edge: #0b0b0b;
    --ink: #f4f4f4;
    --ink-soft: #d9d9d9;
    --icon-glyph: #141414;
  }
  * { margin: 0; padding: 0; box-sizing: border-box; }
  html, body {
    width: 1200px;
    height: 844px;
    overflow: hidden;
    background: var(--backdrop);
    font-family: "Open Sans", Arial, sans-serif;
  }
  .stage {
    position: relative;
    width: 1200px;
    height: 844px;
    display: flex;
    align-items: center;
    justify-content: center;
    gap: 60px;
  }
  .card {
    position: relative;
    width: 520px;
    height: 300px;
    background: var(--card);
    border: 1px solid var(--card-edge);
    color: var(--ink);
  }
  .wordmark {
    position: absolute;
    left: 0;
    right: 0;
    text-align: center;
    font-weight: 400;
    color: var(--ink);
    line-height: 1.15;
  }
  .card--details .wordmark { top: 58px; font-size: 34px; }
  .card--brand .wordmark { top: 100px; font-size: 38px; }
  .contact-list {
    position: absolute;
    right: 26px;
    top: 150px;
    list-style: none;
    font-size: 13px;
    color: var(--ink-soft);
  }
  .contact-list li {
    display: flex;
    align-items: center;
    justify-content: flex-end;
    gap: 8px;
    height: 22px;
  }
  .contact-icon { width: 14px; height: 14px; flex: none; }
  .holder {
    position: absolute;
    left: 30px;
    bottom: 36px;
  }
  .holder-name { font-size: 18px; font-weight: 600; color: var(--ink); }
  .holder-role { font-size: 13px; color: var(--ink-soft); margin-top: 4px; }
</style>
</head>
<body>
<main class="stage">
  <section class="card card--details">
    <p class="wordmark">Mosaic Interior<br>Design</p>
    <ul class="contact-list">
      <li>+447311584209
        <svg class="contact-icon" viewBox="0 0 14 14" aria-hidden="true">
          <rect width="14" height="14" rx="2" fill="var(--ink)"/>
          <path d="M4 3.5c.6-.4 1.2-.2 1.5.4l.5 1c.2.4 0 .8-.3 1l-.4.3c.4.9 1.1 1.6 2 2l.3-.4c.2-.3.6-.5 1-.3l1 .5c.6.3.8.9.4 1.5-.5.7-1.3 1-2.1.7C6 9.5 4.5 8 3.8 6c-.3-.9 0-1.8.2-2.5z" fill="var(--icon-glyph)"/>
        </svg>
      </li>
      <li>petra@mosaicinteriordesign.co.uk
        <svg class="contact-icon" viewBox="0 0 14 14" aria-hidden="true">
          <rect width="14" height="14" rx="2" fill="var(--ink)"/>
          <rect x="3" y="4.5" width="8" height="5.5" rx=".6" fill="var(--icon-glyph)"/>
          <path d="M3.4 5l3.6 2.6L10.6 5" stroke="var(--ink)" stroke-width=".8" fill="none"/>
        </svg>
      </li>
      <li>www.mosaicinteriordesign.co.uk
        <svg class="contact-icon" viewBox="0 0 14 14" aria-hidden="true">
          <rect width="14" height="14" rx="2" fill="var(--ink)"/>
          <path d="M6 8l2-2M5.2 6.6l-1 1a1.6 1.6 0 002.2 2.2l1-1M8.8 7.4l1-1a1.6 1.6 0 00-2.2-2.2l-1 1" stroke="var(--icon-glyph)" stroke-width="1.1" fill="none" stroke-linecap="round"/>
        </svg>
      </li>
    </ul>
    <div class="holder">
      <p class="holder-name">Petra Wendlecombe</p>
      <p class="holder-role">Interior Designer &amp; Stylist</p>
    </div>
  </section>

  <section class="card card--brand">
    <p class="wordmark">Mosaic Interior<br>Design</p>
  </section>
</main>
</body>
</html>
```